LIFE CHANGING NEW WEBSITE DESIGN NEEDED FOR FULL WEBSITE- FUN/FEMININE!

I need a website designed for a personal financial advice website geared at women called BLUE OTTER LANTERN. I will be providing free financial advice around topics of making, saving, spending and sharing money. The concept is to change the way women understand money and the necessity around building various passive income streams to ensure full financial freedom. This will then carry down to advice for mothers with children and children in particular. The website should be elegant and yet witty. I don't want lots of serious photos but more relatable. I will have a photo of myself and my story as this is a blog and needs to be relatable to women and mothers. I like pinks and greys. I want to have a pink piggy bank being broken with a hammer in the front screen to break our traditional mindset around piggy bank saving/spending habits. I have created a logo that is a pink piggy head with BLUE OTTER LANTERN that needs to be incorporated so that it blends into the heading. I have also already started designing the website on Squarespace and can provide access to that. Basically it should have a format of BLUE OTTER LANTERN LOGO center in header then on left hand navigation: MAKE, SAVE, SPEND, SHARE then on right hand header navigation: MISSION, GET STARTED, CONTACT BOL I would like to have the front page when you go to the url to have the image of the piggy bank being broken then a catchy phrase then under 4 boxes with MAKE (image and description) SAVE (image and description) SPEND (image and description) SHARE (image and description) if you click on those or the title they go to pages that are dedicated to each them. Each page should have a little intro on the topic then I want lots of blog links as I will be mainly writing blogs. Each blog site should have ability to write comments as well. I need social media icons on each page too. Please let me know what you need from me to get started. I prefer having a discussion if possible to not waste anyone's time. I need the site to be easy for me to use and add blogs/urls etc as needed. I also need the site to be put into my domain that I already purchased: www.blueotterlantern-sample.com

Target Market(s)

teenage girls, 20 something girls, 30 something girls and mothers

Coding

Coded - Design and coding required

Number of Pages Required

5+ page

Font styles to use
Sans Serif

Colors
e667a6
e34197
f59195
eea4c8
aaaaaa
cbcbcb
959595

Requirements
Must have
• TOP NAVIGATION
• MAKE SAVE SPEND SHARE LOGO/BLUE OTTER LANTERN MISSION GET STARTED CONTACT BOL
• FRONT PAGE: IMAGE OF PIGGY BANK BEING BROKEN WITH A HAMMER
• CATCH PHRASE OVER THE IMAGE
• BUTTON IN PINK- TAKE ACTION (WHICH DIRECTS TO TAKE ACTION TAB ON NAVIGATION HEADER
• 4 BOXES BELOW MAIN IMAGE WITH IMAGE/DESCRIPTIONS FOR MAKE, SAVE, SPEND, SHARE THAT EACH GO TO THE PAGES FROM THE NAVIGATION HEADER
• EACH PAGE SHOULD BE DEDICATED TO THOSE TOPICS THEN THERE IS AN INTRO ON EACH PAGE THEN THE LINKS TO DIFFERENT BLOGS AROUND EACH TOPIC FOR MAKE, SAVE, SPEND, SHARE
• EACH BLOG SHOULD HAVE COMMENTS SECTION AND SOCIAL MEDIA ICONS
• (GOOD TO USE PINKS/GREYS)
Should not have
• BE SUPER BUSY, CLUTTERED, FEEL LIKE I AM SELLING SOMETHING

```html
<!DOCTYPE html>
<html lang="en">
<head>
<meta charset="utf-8">
<title>Blue Otter Lantern</title>
<link rel="stylesheet" href="https://fonts.googleapis.com/css2?family=Lato:wght@400;700;900&display=swap">
<style>
:root{
  --pink:#e34197;
  --pink-soft:#e667a6;
  --coral:#f07f86;
  --ink:#222;
  --grey:#959595;
  --grey-mid:#666;
  --panel:#f2f2f2;
  --chat:#3d3d3d;
  --foot:#111;
  --white:#fff;
}
*{box-sizing:border-box;margin:0;padding:0}
html,body{width:1200px;height:2526px;overflow:hidden;font-family:'Lato',sans-serif;color:var(--ink);background:var(--white)}
.page{position:relative;width:1200px;height:2526px}
.abs{position:absolute}

.site-header{position:absolute;top:0;left:0;width:1200px;height:112px;background:var(--white)}
.nav{position:absolute;top:48px;display:flex;gap:28px;font-size:13.5px;font-weight:700;letter-spacing:.2px}
.nav-left{left:74px}
.nav-right{right:74px}
.brand{position:absolute;top:8px;left:0;width:1200px;text-align:center;color:var(--pink-soft)}
.brand-dot{width:44px;height:44px;border-radius:50%;border:3px solid var(--pink-soft);margin:0 auto 4px}
.brand-name{font-size:26px;font-weight:700;letter-spacing:.5px}

.hero{position:absolute;top:112px;left:0;width:1200px;height:473px;
  background:radial-gradient(ellipse at 55% 60%,#c9505e 0%,#a3594c 30%,#6e5443 60%,#4a3f36 100%)}
.hero-title{position:absolute;top:148px;width:1200px;text-align:center;color:var(--white);font-size:50px;font-weight:900;letter-spacing:.5px}
.btn{display:block;background:var(--pink);color:var(--white);font-weight:900;border-radius:24px;text-align:center;text-transform:uppercase}
.hero-btn{position:absolute;top:220px;left:512px;width:175px;height:44px;line-height:44px;font-size:17px}
.dots{position:absolute;top:350px;left:159px;display:flex;gap:10px}
.dots span{width:10px;height:10px;border-radius:50%;background:#111}
.dots span.on{background:var(--coral)}
.side-social{position:absolute;top:137px;left:1145px;display:flex;flex-direction:column;gap:13px}
.side-social span{width:42px;height:42px;border-radius:8px;display:block}

.topic{position:absolute;top:622px;width:249px;height:321px}
.topic-img{position:absolute;top:0;left:0;width:249px;height:268px}
.topic-bar{position:absolute;bottom:0;left:0;width:249px;height:53px;background:var(--pink);color:var(--white);font-size:19px;font-weight:700;padding:14px 19px}
.topic-bar .go{position:absolute;right:14px;top:13px;width:26px;height:26px;border-radius:50%;background:#111}
.topic-bar .go::after{content:"";position:absolute;left:10px;top:8px;border-left:8px solid var(--white);border-top:5px solid transparent;border-bottom:5px solid transparent}
.topic-open .topic-img{height:158px}
.topic-panel{position:absolute;top:158px;left:0;width:249px;height:163px;background:var(--coral);padding:26px 14px 0 18px}
.topic-panel h3{font-size:19px;font-weight:700;margin-bottom:18px}
.topic-panel p{font-size:13.5px;line-height:22px;text-align:justify}
.topic-panel .drop{position:absolute;right:14px;top:26px;width:26px;height:26px;border-radius:50%;background:#8a8a8a}
.topic-panel .drop::after{content:"";position:absolute;left:7px;top:10px;border-top:7px solid var(--white);border-left:6px solid transparent;border-right:6px solid transparent}

.mission{position:absolute;top:1040px;width:1200px;text-align:center}
.section-title{color:var(--grey-mid);font-weight:900;font-size:48px;letter-spacing:1px}
.mission h4{font-size:23px;font-weight:700;margin-top:4px}
.mission p{width:740px;margin:22px auto 0;font-size:18px;line-height:28px;color:#444}
.mission .btn{width:148px;height:44px;line-height:44px;font-size:17px;margin:34px auto 0}

.blog{position:absolute;top:1416px;left:0;width:1200px;height:476px;background:var(--panel)}
.blog-title{position:absolute;top:58px;width:1200px;text-align:center;font-size:30px;color:var(--grey-mid);font-weight:700}
.post{position:absolute;top:119px;width:331px}
.post-img{height:197px;position:relative}
.post-meta{position:absolute;bottom:18px;left:26px;color:var(--white);font-size:15px;display:flex;align-items:center;gap:8px}
.post-meta i{width:20px;height:16px;border:2px solid var(--white);border-radius:9px;display:block}
.post-share{position:absolute;bottom:12px;right:24px;display:flex;gap:4px}
.post-share span{width:34px;height:34px;border-radius:50%;display:block}
.post h5{font-size:19px;font-weight:400;color:#555;margin-top:22px;letter-spacing:.3px}
.post p{font-size:14.5px;line-height:29px;color:#444;margin-top:6px}

.chat{position:absolute;top:1892px;left:0;width:1200px;height:470px;background:radial-gradient(ellipse at 75% 10%,#4d5049 0%,var(--chat) 50%,#333 100%)}
.chat h2{position:absolute;top:44px;width:1200px;text-align:center;color:var(--white);font-size:48px;font-weight:900}
.field{position:absolute;background:var(--white);font-size:14px;color:#555;padding:15px 11px}
.chat .btn{position:absolute;top:357px;left:526px;width:148px;height:44px;line-height:44px;font-size:17px}

.footer{position:absolute;top:2362px;left:0;width:1200px;height:164px;background:var(--foot);color:var(--white)}
.copy{position:absolute;top:62px;left:76px;font-size:14px}
.foot-social{position:absolute;top:94px;left:76px;display:flex;gap:22px}
.foot-social span{width:22px;height:22px;background:var(--white);border-radius:3px;display:block}
.sub-input{position:absolute;top:84px;left:823px;width:249px;height:40px;background:var(--white);color:#333;font-size:15px;padding:11px 9px}
.sub-go{position:absolute;top:84px;left:1072px;width:53px;height:40px;background:var(--pink);color:var(--white);font-weight:900;font-size:17px;text-align:center;line-height:40px}
</style>
</head>
<body>
<div class="page">

<header class="site-header">
  <nav class="nav nav-left"><span>MAKE</span><span>SAVE</span><span>SPEND</span><span>SHARE</span></nav>
  <div class="brand"><div class="brand-dot"></div><div class="brand-name">Blue Otter Lantern</div></div>
  <nav class="nav nav-right"><span>MISSION</span><span>GET STARTED</span><span>CONTACT BOL</span></nav>
</header>

<section class="hero" role="img" aria-label="Pink piggy bank being broken with a hammer on a wooden table, coins and banknotes spilling out">
  <h1 class="hero-title">BLUE OTTER LANTERN</h1>
  <span class="btn hero-btn">Take Action</span>
  <div class="dots"><span></span><span class="on"></span><span></span><span></span></div>
</section>
<div class="side-social" aria-label="Social links">
  <span style="background:#1d3f86"></span>
  <span style="background:#1da1d8"></span>
  <span style="background:#29379b"></span>
  <span style="background:#e0117f"></span>
</div>

<article class="topic topic-open" style="left:74px">
  <div class="topic-img" role="img" aria-label="Woman in red glasses holding banknotes against a teal background" style="background:linear-gradient(135deg,#3fc3cf,#2aa5b3)"></div>
  <div class="topic-panel"><span class="drop"></span><h3>MAKE</h3><p>Nam libero tempore, cum soluta nobis est eligendi optio cumque nihil impedit quo minus id quod.</p></div>
</article>
<article class="topic" style="left:342px">
  <div class="topic-img" role="img" aria-label="Young woman dropping a coin into a pink piggy bank" style="background:linear-gradient(160deg,#f3efe9,#cfc6c0 60%,#8a9bbd)"></div>
  <div class="topic-bar">SAVE<span class="go"></span></div>
</article>
<article class="topic" style="left:610px">
  <div class="topic-img" role="img" aria-label="Smiling woman shopping on her phone with a bank card" style="background:linear-gradient(160deg,#6a4a3a,#a87858 50%,#c8413f)"></div>
  <div class="topic-bar">SPEND<span class="go"></span></div>
</article>
<article class="topic" style="left:877px">
  <div class="topic-img" role="img" aria-label="Two friends laughing while sharing a phone" style="background:linear-gradient(160deg,#3c5a94,#6b4f3c 55%,#2f63a8)"></div>
  <div class="topic-bar">SHARE<span class="go"></span></div>
</article>

<section class="mission">
  <h2 class="section-title">MISSION</h2>
  <h4>Welcome to Blue Otter Lantern</h4>
  <p>My mission is simple- I want to challenge you to rethink the way you think about growing, spending and saving money. By redesigning your life around your finances I want you to run your life as if you are the CEO of your own business, and the business is maximising the value and profitability of your life.</p>
  <span class="btn">Read More</span>
</section>

<section class="blog">
  <h2 class="blog-title">BLOG</h2>
  <article class="post" style="left:74px">
    <div class="post-img" role="img" aria-label="Hand breaking a white piggy bank with a hammer, banknotes inside" style="background:linear-gradient(135deg,#707070,#4e4e4e)">
      <div class="post-meta"><i></i>23</div>
      <div class="post-share"><span style="background:#1a2fb0"></span><span style="background:#1da1f2"></span><span style="background:#2332a8"></span></div>
    </div>
    <h5>LOREM IPSUM DOLOR</h5>
    <p>Sed ut perspiciatis unde omnis iste natus error sit voluptatem accusantium doloremque laudan-tium, totam rem aperiam,</p>
  </article>
  <article class="post" style="left:435px">
    <div class="post-img" role="img" aria-label="Calculator, pen and finance report beside a piggy bank" style="background:linear-gradient(135deg,#dfe6ef,#3d7fa0 45%,#f2dcd0)">
      <div class="post-meta"><i></i>23</div>
      <div class="post-share"><span style="background:#1a2fb0"></span><span style="background:#1da1f2"></span><span style="background:#2332a8"></span></div>
    </div>
    <h5>LOREM IPSUM DOLOR</h5>
    <p>Sed ut perspiciatis unde omnis iste natus error sit voluptatem accusantium doloremque laudan-tium, totam rem aperiam,</p>
  </article>
  <article class="post" style="left:796px">
    <div class="post-img" role="img" aria-label="Person putting a coin into a white piggy bank on a wooden table" style="background:linear-gradient(135deg,#5a4530,#b78034 50%,#8a6a4a)">
      <div class="post-meta"><i></i>23</div>
      <div class="post-share"><span style="background:#1a2fb0"></span><span style="background:#1da1f2"></span><span style="background:#2332a8"></span></div>
    </div>
    <h5>LOREM IPSUM DOLOR</h5>
    <p>Sed ut perspiciatis unde omnis iste natus error sit voluptatem accusantium doloremque laudan-tium, totam rem aperiam,</p>
  </article>
</section>

<section class="chat">
  <h2>LET’S CHAT</h2>
  <div class="field" style="left:254px;top:131px;width:333px;height:48px">Enter Name</div>
  <div class="field" style="left:614px;top:131px;width:333px;height:48px">Subject</div>
  <div class="field" style="left:254px;top:191px;width:692px;height:48px">Enter Email Address</div>
  <div class="field" style="left:254px;top:250px;width:692px;height:88px">Message</div>
  <span class="btn">Submit</span>
</section>

<footer class="footer">
  <div class="copy">©2019 www.blueotterlantern-sample.com</div>
  <div class="foot-social" aria-label="Social links"><span></span><span></span><span></span><span></span><span></span></div>
  <div class="sub-input">Enter Email Address</div>
  <div class="sub-go">GO</div>
</footer>

</div>
</body>
</html>
```